Food broker, trader, wholesaler, liquidator looking for a 5 pages website

Looking for a 5 pages website design. We are food brokers, traders, wholesaler and closeout buyer working with manufacturers, distributors, importers sell to retailers, food service operators and industrial (ingredients). We help market their products. We are a resource for those who need a solution in the distribution/selling/placement of food on the shelves, kitchens and pantries. Whether we open new accounts with new products or sell short dated inventory, we know where to go and get results.

Target Market(s)

Food manufacturers, food distributors, food brokers

Coding

Coded - Design and coding required

Number of Pages Required

4 page

Font styles to use
Serif

Requirements
Must have
• Food-food production-warehouse-Food packaging-people meeting-trucks-supermarket shelves-

```html
<!DOCTYPE html>
<html lang="en">
<head>
<meta charset="utf-8">
<title>Harborline Provisions</title>
<link href="https://fonts.googleapis.com/css2?family=Libre+Baskerville:wght@400;700&family=Montserrat:wght@500;600;700&family=Open+Sans:wght@400;600&display=swap" rel="stylesheet">
<style>
:root{
  --navy:#1b1d74;
  --navy-deep:#121460;
  --heading:#262a6b;
  --label:#5a5fa3;
  --text:#4a4a4a;
  --white:#ffffff;
  --dark-sea:#0a1a1e;
  --pale:#eef0f5;
}
*{margin:0;padding:0;box-sizing:border-box}
html,body{width:1200px;height:3412px;overflow:hidden}
body{position:relative;background:var(--white);font-family:"Open Sans",sans-serif;color:var(--text)}
.abs{position:absolute}
.serif{font-family:"Libre Baskerville",serif;font-weight:700}
.center{text-align:center;left:0;width:1200px}

/* header */
.site-header{top:0;left:0;width:1200px;height:93px;background:var(--white)}
.brand{left:93px;top:20px;display:flex;align-items:center;gap:12px}
.brand-dot{width:52px;height:52px;border-radius:50%;background:var(--navy)}
.brand-name{font-family:"Libre Baskerville",serif;font-weight:700;font-size:19px;color:var(--navy);letter-spacing:.3px}
.main-nav a{position:absolute;top:40px;font-family:"Montserrat",sans-serif;font-size:14px;font-weight:600;color:#8a8a9a;text-decoration:none;letter-spacing:.3px}
.main-nav a.active{color:var(--navy)}
.nav-marker{left:526px;top:0;width:66px;height:4px;background:var(--navy)}

/* hero */
.hero{top:93px;left:0;width:1200px;height:598px;background:linear-gradient(110deg,#8a6a48 0%,#a98a62 18%,#5b7fb8 40%,#c9d2dd 62%,#2e5fa8 82%,#b48b55 100%)}
.hero-box{left:94px;top:250px;width:444px;height:293px;background:rgba(27,29,116,.88)}
.hero-kicker{top:305px;left:94px;width:444px;text-align:center;font-family:"Libre Baskerville",serif;font-size:24px;color:var(--white);letter-spacing:.5px}
.hero-title{top:336px;left:94px;width:444px;text-align:center;font-family:"Libre Baskerville",serif;font-weight:700;font-size:42px;line-height:48px;color:var(--white)}
.btn{position:absolute;border-radius:30px;font-family:"Montserrat",sans-serif;font-weight:600;font-size:16px;display:flex;align-items:center;justify-content:center;letter-spacing:.3px}
.btn-light{border:2px solid var(--white);color:var(--white)}
.btn-navy{border:2px solid var(--navy);color:var(--navy)}
.slider-dots{top:647px;left:562px;display:flex;gap:9px}
.slider-dots span{width:13px;height:13px;border-radius:50%;background:var(--white)}
.slider-dots span.current{background:transparent;border:2px solid var(--white)}

/* section titles */
.section-title{font-family:"Libre Baskerville",serif;font-weight:700;font-size:29px;color:var(--heading);letter-spacing:.3px}
.title-rule{height:3px;width:56px;background:var(--heading)}

.about-copy{top:836px;left:150px;width:900px;text-align:center;font-size:18px;line-height:27px;color:#555}
.about-copy p+p{margin-top:11px}

/* what we do */
.service-title{font-family:"Montserrat",sans-serif;font-weight:700;font-size:20px;color:var(--white);letter-spacing:.3px;text-align:center}
.service-text{font-size:14px;line-height:23px;color:#dfe1f3;text-align:center}
.service-divider{width:1px;height:239px;top:1315px;background:rgba(255,255,255,.35)}

/* giving back */
.give-title{left:158px;top:2336px;font-family:"Libre Baskerville",serif;font-weight:700;font-size:29px;color:var(--white)}
.give-copy{left:160px;top:2410px;width:390px;font-size:16px;line-height:27px;color:#d8dde0}
.give-copy p+p{margin-top:11px}

/* contact */
.contact-bg{top:2706px;left:0;width:1200px;height:522px;background:linear-gradient(160deg,#f3f4f8 0%,#e3e6ee 50%,#f5f6f9 100%)}
.contact-intro{top:2910px;font-size:16px;line-height:28px;color:var(--navy)}
.contact-icon{width:72px;height:72px;border-radius:50%;background:var(--navy);display:flex;align-items:center;justify-content:center}
.contact-label{font-size:15px;color:var(--navy);letter-spacing:.2px}
.contact-value{font-size:19px;font-weight:600;color:var(--navy);line-height:26px;margin-top:4px}

/* footer */
.site-footer{top:3228px;left:0;width:1200px;height:184px;background:var(--navy)}
.social{top:3261px;left:515px;display:flex;gap:6px}
.social span{width:35px;height:35px;border-radius:50%;border:1.5px solid var(--white)}
.footer-nav a{position:absolute;top:3316px;font-family:"Montserrat",sans-serif;font-weight:600;font-size:14px;color:var(--white);text-decoration:none}
.copyright{top:3349px;font-size:12px;color:#d0d2ee}
</style>
</head>
<body>

<header class="abs site-header">
  <div class="abs brand"><span class="brand-dot"></span><span class="brand-name">HARBORLINE PROVISIONS</span></div>
  <div class="abs nav-marker"></div>
  <nav class="main-nav">
    <a class="active" style="left:538px">HOME</a>
    <a style="left:626px">ABOUT US</a>
    <a style="left:747px">WHAT WE DO</a>
    <a style="left:891px">CONTACT</a>
    <a style="left:1005px">GIVING BACK</a>
  </nav>
</header>

<section>
  <div class="abs hero" role="img" aria-label="Photo of a large warehouse aisle with blue pallet racks stacked with boxed goods"></div>
  <div class="abs hero-box"></div>
  <div class="abs hero-kicker">WELCOME TO</div>
  <div class="abs hero-title">HARBORLINE<br>PROVISIONS</div>
  <div class="btn btn-light" style="left:232px;top:450px;width:172px;height:52px">LEARN MORE</div>
  <div class="abs slider-dots"><span class="current"></span><span></span><span></span><span></span></div>
</section>

<section>
  <div class="abs center section-title" style="top:762px">ABOUT HARBORLINE PROVISIONS</div>
  <div class="abs title-rule" style="top:802px;left:570px"></div>
  <div class="abs about-copy">
    <p>Harborline Provisions works with food manufacturers, brand owners, distributors and wholesalers market their products. Retail, Food Service and Industrial ingredients.</p>
    <p>Founded in 2008, Harborline Provisions started with the distribution of gluten free products understanding the need to provide access to unique flavors and products for the celiac consumers. From this, we expanded into deli, dairy, groceries, frozen and beverages.</p>
  </div>
  <div class="btn btn-navy" style="left:503px;top:1019px;width:190px;height:55px">LEARN MORE</div>
</section>

<section>
  <svg class="abs" style="top:1144px;left:0" width="1200" height="518" role="img" aria-label="Photo of food factory workers in hairnets, tinted deep blue">
    <defs><linearGradient id="wwdFill" x1="0" y1="0" x2="1" y2="1"><stop offset="0" stop-color="#1a1d78"/><stop offset=".5" stop-color="#23288a"/><stop offset="1" stop-color="#14176a"/></linearGradient></defs>
    <polygon points="0,61 600,0 1200,61 1200,459 600,518 0,459" fill="url(#wwdFill)"/>
  </svg>
  <div class="abs center serif" style="top:1210px;font-size:29px;color:var(--white)">WHAT WE DO</div>
  <div class="abs title-rule" style="top:1254px;left:570px;background:var(--white)"></div>

  <svg class="abs" style="left:241px;top:1345px" width="76" height="60" fill="none" stroke="#fff" stroke-width="2.5">
    <rect x="2" y="2" width="72" height="46" rx="3"/><line x1="2" y1="40" x2="74" y2="40"/><line x1="28" y1="56" x2="48" y2="56"/><line x1="38" y1="48" x2="38" y2="56"/>
    <polyline points="12,30 24,18 34,26 46,12 56,22 64,14"/>
  </svg>
  <div class="abs service-title" style="left:132px;top:1436px;width:300px">SALES &amp; MARKETING</div>
  <div class="abs service-text" style="left:152px;top:1474px;width:260px">we connect food buyers and sellers through a dedicated approach.</div>

  <div class="abs service-divider" style="left:442px"></div>

  <svg class="abs" style="left:559px;top:1342px" width="76" height="76" fill="none" stroke="#fff" stroke-width="2.5">
    <polygon points="38,24 50,31 50,45 38,52 26,45 26,31"/>
    <circle cx="38" cy="6" r="5"/><circle cx="70" cy="38" r="5"/><circle cx="6" cy="38" r="5"/><circle cx="38" cy="70" r="5"/>
    <circle cx="15" cy="15" r="5"/><circle cx="61" cy="15" r="5"/><circle cx="15" cy="61" r="5"/><circle cx="61" cy="61" r="5"/>
    <line x1="38" y1="11" x2="38" y2="24"/><line x1="38" y1="52" x2="38" y2="65"/><line x1="11" y1="38" x2="26" y2="38"/><line x1="50" y1="38" x2="65" y2="38"/>
  </svg>
  <div class="abs service-title" style="left:447px;top:1436px;width:300px">TRADING</div>
  <div class="abs service-text" style="left:472px;top:1474px;width:260px">we purchase goods anywhere and ship them Nationwide and Export.</div>

  <div class="abs service-divider" style="left:759px"></div>

  <svg class="abs" style="left:888px;top:1346px" width="70" height="70" fill="none" stroke="#fff" stroke-width="2.5">
    <rect x="2" y="6" width="44" height="60" rx="2"/><rect x="14" y="2" width="20" height="9"/>
    <polyline points="9,24 12,27 17,21"/><line x1="22" y1="24" x2="38" y2="24"/>
    <polyline points="9,36 12,39 17,33"/><line x1="22" y1="36" x2="38" y2="36"/>
    <polyline points="9,48 12,51 17,45"/><line x1="22" y1="48" x2="38" y2="48"/>
    <rect x="40" y="2" width="28" height="22"/><line x1="40" y1="12" x2="68" y2="12"/><rect x="46" y="38" width="20" height="26"/>
  </svg>
  <div class="abs service-title" style="left:773px;top:1436px;width:300px">EXCESS INVENTORY</div>
  <div class="abs service-text" style="left:793px;top:1471px;width:265px">We buy closeouts and excess inventory for prisons, outlet stores and discounters.</div>
</section>

<section>
  <div class="abs center section-title" style="top:1710px">OUR CYCLE</div>
  <div class="abs title-rule" style="top:1751px;left:567px"></div>
  <svg class="abs" style="left:0;top:1780px" width="1200" height="440" viewBox="0 1780 1200 440" font-family="Montserrat, sans-serif" font-weight="700" font-size="12.5" fill="#5a5fa3">
    <circle cx="593" cy="1943" r="128" fill="#fff" stroke="#f0f0f3" stroke-width="4"/>
    <circle cx="593" cy="1943" r="167" fill="none" stroke="#c7c9e0" stroke-width="2" stroke-dasharray="7 6"/>
    <circle cx="593" cy="1943" r="94" fill="#1b1d74"/>
    <text x="593" y="1938" text-anchor="middle" font-family="Libre Baskerville, serif" font-size="15" fill="#fff">HARBORLINE</text>
    <text x="593" y="1960" text-anchor="middle" font-family="Libre Baskerville, serif" font-size="15" fill="#fff">PROVISIONS</text>
    <g fill="#fff" stroke="#3a3f86" stroke-width="2">
      <circle cx="469" cy="1828" r="8"/><circle cx="711" cy="1826" r="8"/><circle cx="426" cy="1935" r="8"/><circle cx="754" cy="1935" r="8"/>
      <circle cx="461" cy="2056" r="8"/><circle cx="719" cy="2054" r="8"/><circle cx="595" cy="2111" r="8"/>
    </g>
    <g fill="none" stroke="#1b1d74" stroke-width="2.2">
      <!-- food -->
      <path d="M402 1810h40v8h-40zM406 1818v18h32v-18M412 1810v-4h20v4M422 1818v18"/>
      <!-- supermarket -->
      <rect x="739" y="1809" width="36" height="34"/><line x1="739" y1="1820" x2="775" y2="1820"/><line x1="739" y1="1831" x2="775" y2="1831"/><line x1="748" y1="1809" x2="748" y2="1843"/><line x1="762" y1="1809" x2="762" y2="1843"/>
      <!-- food production -->
      <path d="M358 1948v-22l4-8v-6h6v6l4 8v22zM375 1948v-22l4-8v-6h6v6l4 8v22zM392 1948v-22l4-8v-6h6v6l4 8v22zM354 1952h54"/>
      <!-- trucks -->
      <path d="M778 1925h28v22h-28zM778 1933h-12l-6 8v6h18"/><circle cx="768" cy="1949" r="4"/><circle cx="798" cy="1949" r="4"/>
      <!-- warehouse -->
      <path d="M401 2086v-28l20-12 20 12v28zM411 2086v-20h20v20M411 2074h20M421 2066v20"/>
      <!-- people -->
      <circle cx="748" cy="2058" r="6"/><circle cx="764" cy="2058" r="6"/><circle cx="756" cy="2070" r="6"/><path d="M742 2086c0-8 6-10 14-10s14 2 14 10"/>
      <!-- packaging -->
      <path d="M577 2136l18-8 18 8v22l-18 8-18-8zM577 2136l18 8 18-8M595 2144v22"/><path d="M600 2154c4-4 8-4 9-2"/>
    </g>
    <text x="385" y="1829" text-anchor="end">FOOD</text>
    <text x="788" y="1826">SUPERMARKET</text><text x="788" y="1842">SHELVES</text>
    <text x="338" y="1940" text-anchor="end">FOOD</text><text x="338" y="1956" text-anchor="end">PRODUCTION</text>
    <text x="832" y="1948">TRUCKS</text>
    <text x="385" y="2092" text-anchor="end">WAREHOUSE</text>
    <text x="793" y="2088">PEOPLE MEETING</text>
    <text x="598" y="2190" text-anchor="middle">FOOD PACKAGING</text>
  </svg>
</section>

<div class="abs contact-bg" role="img" aria-label="Faint photo of a light warehouse interior"></div>

<section>
  <svg class="abs" style="top:2232px;left:0" width="1200" height="545">
    <defs>
      <clipPath id="giveClip"><polygon points="0,0 1200,0 1200,474 600,545 0,474"/></clipPath>
      <linearGradient id="shipFill" x1="0" y1="0" x2="1" y2="1"><stop offset="0" stop-color="#3b6fa8"/><stop offset=".35" stop-color="#c8414f"/><stop offset=".6" stop-color="#e08a3a"/><stop offset=".8" stop-color="#2b5ea5"/><stop offset="1" stop-color="#d23f63"/></linearGradient>
    </defs>
    <polygon points="0,0 1200,0 1200,474 600,545 0,474" fill="#0a1a1e"/>
    <g clip-path="url(#giveClip)">
      <polygon points="530,50 720,50 1200,300 1200,460 820,510 560,200" fill="url(#shipFill)" role="img" aria-label="Aerial photo of a cargo ship loaded with colorful shipping containers"/>
    </g>
  </svg>
  <div class="abs give-title">GIVING BACK</div>
  <div class="abs title-rule" style="top:2377px;left:160px;width:56px;height:2px;background:var(--white)"></div>
  <div class="abs give-copy">
    <p>Augiat in pede Fusce tellus Sed metus augue convallis et vehicula ut pulvinar eu ante Integer</p>
    <p>Auscipit leo massa sodales velit et scelerisque mi tortor at ipsum Proin orci odio commodo ac gravida non tristique vel te Curabitur iaculis tempu</p>
  </div>
  <div class="btn btn-light" style="left:159px;top:2585px;width:167px;height:50px;font-size:15px">LEARN MORE</div>
</section>

<section>
  <div class="abs center section-title" style="top:2854px">CONTACT US</div>
  <div class="abs title-rule" style="top:2896px;left:570px"></div>
  <div class="abs center contact-intro">Augiat in pede Fusce tellus Sed metus augue convallis et vehicula ut pulvinar eu ante<br>Integer orci tellus tristique vitae</div>

  <div class="abs contact-icon" style="left:206px;top:3034px">
    <svg width="34" height="34" viewBox="0 0 24 24" fill="#fff"><path d="M6.6 10.8a15.1 15.1 0 0 0 6.6 6.6l2.2-2.2c.3-.3.7-.4 1-.2 1.1.4 2.3.6 3.6.6.6 0 1 .4 1 1V20c0 .6-.4 1-1 1C10.6 21 3 13.4 3 4c0-.6.4-1 1-1h3.5c.6 0 1 .4 1 1 0 1.3.2 2.5.6 3.6.1.3 0 .7-.2 1z"/></svg>
  </div>
  <div class="abs" style="left:294px;top:3036px"><div class="contact-label">PHONE NUMBER</div><div class="contact-value" style="font-size:21px">(555) 014 2288</div></div>

  <div class="abs contact-icon" style="left:495px;top:3034px">
    <svg width="34" height="26" viewBox="0 0 34 26" fill="#fff"><rect x="0" y="0" width="34" height="26" rx="2"/><polyline points="1,2 17,14 33,2" fill="none" stroke="#1b1d74" stroke-width="2.5"/></svg>
  </div>
  <div class="abs" style="left:583px;top:3036px"><div class="contact-label">EMAIL US</div><div class="contact-value">info@harborline.com</div></div>

  <div class="abs contact-icon" style="left:809px;top:3026px">
    <svg width="28" height="38" viewBox="0 0 24 32" fill="#fff"><path d="M12 0C5.4 0 0 5.4 0 12c0 9 12 20 12 20s12-11 12-20C24 5.4 18.6 0 12 0zm0 17a5 5 0 1 1 0-10 5 5 0 0 1 0 10z"/></svg>
  </div>
  <div class="abs" style="left:897px;top:3028px"><div class="contact-label">ADDRESS</div><div class="contact-value" style="font-weight:400;font-size:18px">245 Meridian Avenue<br>Suite 4 Austin TX 78701</div></div>
</section>

<footer class="abs site-footer"></footer>
<div class="abs social"><span></span><span></span><span></span><span></span></div>
<nav class="footer-nav">
  <a style="left:308px">HOME</a>
  <a style="left:397px">ABOUT US</a>
  <a style="left:517px">WHAT WE DO</a>
  <a style="left:662px">CONTACT</a>
  <a style="left:775px">GIVING BACK</a>
</nav>
<div class="abs center copyright">© 2020 Company Name | All Rights Reserved | Disclaimer</div>

</body>
</html>
```